Realty Group Needs Classy, Contemporary Letterhead Design

We need a letterhead design for a new realty company located in NY, USA. We buy investment properties to rehabilitate and or keep in our rental portfolio.

```html
<!DOCTYPE html>
<html lang="en">
<head>
<meta charset="UTF-8">
<title>Meridian Realty Group – Letterhead</title>
<link rel="stylesheet" href="https://fonts.googleapis.com/css2?family=Montserrat:wght@800&family=Raleway:wght@400;600;700&display=swap">
<style>
  :root {
    --purple: #522a8a;
    --grey-band: #7d7d7d;
    --ink: #222222;
    --paper: #ffffff;
    --backdrop: #e6e6e6;
    --signature-tone: #ececec;
  }
  html, body {
    margin: 0;
    width: 1200px;
    height: 803px;
    overflow: hidden;
    background: var(--backdrop);
  }
  .canvas {
    position: relative;
    width: 1200px;
    height: 803px;
  }
  .letterhead {
    position: absolute;
    left: 327px;
    top: 16px;
    width: 800px;
    height: 1128px;
    background: var(--paper);
    transform: scale(0.6835);
    transform-origin: top left;
    box-shadow: 0 6px 18px rgba(0,0,0,0.18);
    overflow: hidden;
    font-family: "Raleway", sans-serif;
    color: var(--ink);
  }
  .decor {
    position: absolute;
    inset: 0;
    width: 800px;
    height: 1128px;
  }
  .brand {
    position: absolute;
    left: 62px;
    top: 100px;
    display: flex;
    align-items: center;
    gap: 12px;
  }
  .brand-dot {
    width: 22px;
    height: 22px;
    border-radius: 50%;
    background: var(--purple);
  }
  .brand-name {
    font-family: "Montserrat", sans-serif;
    font-weight: 800;
    font-size: 29px;
    color: var(--purple);
    letter-spacing: 0.2px;
  }
  .letter-body {
    position: absolute;
    left: 62px;
    top: 234px;
    width: 660px;
    font-size: 13.6px;
    line-height: 17.6px;
  }
  .letter-body p {
    margin: 0 0 17.6px;
    text-align: justify;
  }
  .letter-body .greeting {
    text-align: left;
  }
  .sign-off {
    position: absolute;
    left: 62px;
    top: 838px;
    font-size: 13.6px;
  }
  .signature {
    position: absolute;
    left: 86px;
    top: 864px;
    width: 124px;
    height: 76px;
    background: var(--signature-tone);
    border-radius: 4px;
  }
  .signatory {
    position: absolute;
    left: 62px;
    top: 948px;
    font-size: 13.6px;
    font-weight: 700;
  }
  .footer-rule {
    position: absolute;
    left: 70px;
    top: 1040px;
    width: 660px;
    height: 1.5px;
    background: var(--purple);
  }
  .contact {
    position: absolute;
    top: 1060px;
    display: flex;
    align-items: center;
    gap: 10px;
    font-size: 12.4px;
    line-height: 16px;
  }
  .contact svg {
    width: 22px;
    height: 22px;
    flex: none;
  }
  .contact-address { left: 122px; }
  .contact-phone { left: 354px; }
  .contact-web { left: 518px; }
</style>
</head>
<body>
<main class="canvas">
  <section class="letterhead">
    <svg class="decor" viewBox="0 0 800 1128" aria-hidden="true">
      <!-- top-right swoosh -->
      <path d="M410 0 C640 15 770 110 800 218 L800 0 Z" fill="var(--grey-band)"/>
      <path d="M548 0 C690 20 775 95 800 166 L800 0 Z" fill="var(--purple)" stroke="#ffffff" stroke-width="3"/>
      <!-- bottom-left swoosh -->
      <path d="M0 978 C20 1060 80 1110 158 1128 L0 1128 Z" fill="var(--purple)"/>
      <path d="M0 1040 C40 1090 100 1115 150 1128 L0 1128 Z" fill="var(--grey-band)" stroke="#ffffff" stroke-width="3"/>
      <!-- bottom-right swoosh -->
      <path d="M800 1038 C770 1080 730 1110 686 1128 L800 1128 Z" fill="var(--purple)"/>
      <path d="M800 1074 C780 1090 745 1110 706 1128 L800 1128 Z" fill="var(--grey-band)" stroke="#ffffff" stroke-width="3"/>
    </svg>

    <header class="brand">
      <span class="brand-dot"></span>
      <span class="brand-name">Meridian Realty Group, LLC</span>
    </header>

    <article class="letter-body">
      <p class="greeting">Lorem Ipsum is simply</p>
      <p>Dummy text of the printing and typesetting industry. Lorem Ipsum has been the industry's standard dummy text ever since the 1500s, when an unknown printer took a galley of type and scrambled it to make a type specimen book. It has survived not only five centuries, but also the leap into electronic typesetting, remaining essentially unchanged. It was popularised in the 1960s with the release of Letraset sheets containing Lorem Ipsum passages, and more recently with desktop publishing software like Aldus PageMaker including versions of Lorem Ipsum.</p>
      <p>Lorem Ipsum is simply dummy text of the printing and typesetting industry. Lorem Ipsum has been the industry's standard dummy text ever since the 1500s, when an unknown printer took a galley of type and scrambled it to make a type specimen book. It has survived not only five centuries, but also the leap into electronic typesetting, remaining essentially unchanged. It was popularised in the 1960s with the release of Letraset sheets containing Lorem Ipsum passages, and more recently with desktop publishing software like Aldus PageMaker including versions of Lorem Ipsum.</p>
      <p>Lorem Ipsum is simply dummy text of the printing and typesetting industry. Lorem Ipsum has been the industry's standard dummy text ever since the 1500s, when an unknown printer took a galley of type and scrambled it to make a type specimen book. It has survived not only five centuries, but also the leap into electronic typesetting, remaining essentially unchanged. It was popularised in the 1960s with the release of Letraset sheets containing Lorem Ipsum passages, and more recently with desktop publishing software like Aldus PageMaker including versions of Lorem Ipsum.</p>
      <p>Lorem Ipsum is simply dummy text of the printing and typesetting industry. Lorem Ipsum has been the industry's standard dummy text ever since the 1500s, when an unknown printer took a galley of type and scrambled it to make a type specimen book. It has survived not only five centuries, but also the leap into electronic typesetting, remaining essentially unchanged. It was popularised in the 1960s with the release of Letraset sheets containing Lorem Ipsum passages, and more recently with desktop publishing software like Aldus PageMaker including versions of Lorem Ipsum.Lorem Ipsum is simply dummy text of the printing and typesetting industry. Lorem Ipsum has been the industry's standard dummy text ever since the 1500s, when an unknown printer took a galley of type and scrambled it to make a type specimen book.</p>
    </article>

    <div class="sign-off">Lorem Ipsum Dummy Text</div>
    <div class="signature" role="img" aria-label="Handwritten signature"></div>
    <div class="signatory">Lorem Ipsum Dummy Text</div>

    <div class="footer-rule"></div>

    <div class="contact contact-address">
      <svg viewBox="0 0 24 24" fill="none" stroke="var(--purple)" stroke-width="1.4">
        <path d="M12 21s-6-6.2-6-11a6 6 0 0 1 12 0c0 4.8-6 11-6 11z"/>
        <circle cx="12" cy="10" r="2.3"/>
        <path d="M5 21h14"/>
      </svg>
      <span>123, Your Address Goes Here,<br>NY, USA- 123456</span>
    </div>
    <div class="contact contact-phone">
      <svg viewBox="0 0 24 24" fill="none" stroke="var(--purple)" stroke-width="1.4">
        <circle cx="12" cy="12" r="10.5"/>
        <path d="M8.5 7.5l2 2-1.2 1.4c.8 1.6 2.1 2.9 3.7 3.7l1.4-1.2 2 2-1.4 1.4c-3.6-.5-6.9-3.8-7.4-7.4z"/>
      </svg>
      <span>+0123 456 789<br>+0123 456 789</span>
    </div>
    <div class="contact contact-web">
      <svg viewBox="0 0 24 24" fill="none" stroke="var(--purple)" stroke-width="1.4">
        <circle cx="12" cy="12" r="10"/>
        <ellipse cx="12" cy="12" rx="4.5" ry="10"/>
        <path d="M2 12h20M4 7h16M4 17h16"/>
      </svg>
      <span>info@yourmailid.com<br>www.yourwebsite.com</span>
    </div>
  </section>
</main>
</body>
</html>
```